Verdant Ledger - Paid Surveys publisher portal

• Homepage
• Blank Sub Page (Where content goes in between the header/footer)
• Publisher Application Page, complete with Form
• Survey Wall page

Sites that are in a similar vertical that have interesting designs:
rovabin.com
quillmarsh.com
dovek.com
tarn.io

This is a business-to-business site, and needs to have this type of feel to it. Focus on generating revenue, offer completion, paid surveys is the market.

Format: HTML/CSS

Link to current version of application, and form:
https://gridwaveform.brokelqest.com
https://gridwaveform.brokelqest.com/apply
https://gridwaveform.brokelqest.com/panel/4/morvath_user

Please note that we are changing the brand of this project, the name will be determined shortly but everything else remains. It will likely be Verdant Ledger instead of GridWaveform. We will confirm.

Industry/Entity Type

Market Research

Coding

Coded - Design and coding required

Number of Pages Required

4 page

Font styles to use
Sans Serif

Colors

Designer to choose colors to be used in the design.

```html
<!DOCTYPE html>
<html lang="en">
<head>
<meta charset="utf-8">
<title>GridWaveform — Business 2 Business Solutions</title>
<link rel="stylesheet" href="https://fonts.googleapis.com/css2?family=Montserrat:wght@400;500;600;700&family=Mulish:wght@400;600;700&display=swap">
<style>
:root{
  --navy:#1b2a44;
  --navy-deep:#15223a;
  --blue:#2196e6;
  --ink:#1d2330;
  --text:#555b66;
  --muted:#8a8f98;
  --grey-bg:#f2f2f2;
  --strip:#ebebeb;
  --card:#efefef;
  --white:#ffffff;
  --date-blue:#2196e6;
  --date-red:#d8262d;
}
*{box-sizing:border-box;margin:0;padding:0}
html,body{width:1200px;height:3364px;overflow:hidden}
body{position:relative;font-family:'Mulish',sans-serif;color:var(--text);background:var(--white)}
section,header,footer,aside{position:absolute;left:0;width:1200px}
h1,h2,h3,h4{font-family:'Montserrat',sans-serif;color:var(--ink)}
.btn{display:inline-flex;align-items:center;justify-content:center;background:var(--navy);color:#fff;font-family:'Montserrat',sans-serif;font-weight:700;font-size:14px;letter-spacing:.5px;border-radius:22px;text-transform:uppercase}

/* hero */
.hero{top:0;height:543px;background:linear-gradient(120deg,#2a3038 0%,#3d4550 45%,#262b33 100%)}
.hero-photo{position:absolute;inset:0;background:radial-gradient(ellipse at 55% 40%,rgba(120,110,100,.45),rgba(20,25,32,.2) 70%)}
.hero h1{position:absolute;top:206px;width:100%;text-align:center;color:#fff;font-size:40px;font-weight:600}
.hero p{position:absolute;top:270px;width:100%;text-align:center;color:#e8e8e8;font-size:20px;font-family:'Montserrat',sans-serif}
.slider-dots{position:absolute;left:1128px;top:270px;display:flex;flex-direction:column;gap:9px}
.slider-dots span{width:10px;height:10px;border-radius:50%;border:2px solid var(--blue)}
.slider-dots span:first-child{background:#d7d7d7;border-color:#d7d7d7}
.sidebar{position:absolute;left:0;top:0;width:77px;height:543px;background:var(--navy)}
.brand{position:absolute;left:14px;top:18px;display:flex;align-items:center;gap:12px}
.brand-dot{width:50px;height:50px;border-radius:50%;background:var(--blue)}
.brand-name{font-family:'Montserrat',sans-serif;font-weight:700;font-size:22px;color:#fff}
.side-nav{position:absolute;left:0;top:96px;width:77px;display:flex;flex-direction:column;align-items:center;gap:20px}
.side-nav span{width:36px;height:36px;display:flex;align-items:center;justify-content:center;border-radius:50%}
.side-nav span.active{border:2px solid var(--date-red)}

/* about */
.about{top:543px;height:480px;background:#fff;overflow:hidden}
.about-blue{position:absolute;inset:0}
.about-photo{position:absolute;left:76px;top:65px;width:566px;height:355px;background:linear-gradient(135deg,#6a6f78,#b9b6b2 55%,#e3e1de);box-shadow:0 6px 18px rgba(0,0,0,.25)}
.play{position:absolute;left:258px;top:150px;width:50px;height:50px;background:rgba(255,255,255,.8);display:flex;align-items:center;justify-content:center}
.about h2{position:absolute;left:676px;top:92px;font-size:34px;font-weight:700}
.about p{position:absolute;left:678px;top:165px;width:430px;font-size:14px;line-height:23px}
.about .btn{position:absolute;left:686px;top:337px;width:130px;height:38px}

/* services */
.services{top:1023px;height:535px;background:var(--grey-bg);text-align:center}
.sec-title{font-size:30px;font-weight:700;text-align:center}
.sec-rule{width:42px;height:3px;background:var(--navy);margin:10px auto 0}
.services h2{padding-top:44px}
.services .lead{width:900px;margin:16px auto 0;font-size:15px;line-height:25px}
.svc-row{position:absolute;top:200px;left:0;width:1200px;display:flex;justify-content:center;gap:60px}
.svc{width:282px}
.svc h3{font-size:16px;font-weight:700;margin-top:20px}
.svc p{font-size:13.5px;line-height:23px;margin-top:8px}
.services .btn.view{position:absolute;left:474px;top:387px;width:252px;height:50px;font-size:21px;font-weight:500;text-transform:none;letter-spacing:0;border-radius:26px}
.dots{position:absolute;top:488px;left:0;width:1200px;display:flex;justify-content:center;gap:11px}
.dots span{width:7px;height:7px;border-radius:50%;background:var(--navy)}

/* partners */
.partners{top:1558px;height:120px;background:var(--strip);display:flex;align-items:center;justify-content:space-between;padding:0 74px}
.partners ul{list-style:none;display:flex;gap:58px;align-items:center}
.partners li{font-family:'Montserrat',sans-serif;font-weight:600;font-size:17px;color:#666}

/* news */
.news{top:1678px;height:614px;background:#fff}
.news h2{padding-top:40px}
.cards{position:absolute;top:139px;left:76px;display:flex;gap:21px}
.card{width:336px;height:420px;background:var(--card)}
.card-img{height:186px}
.card-body{padding:20px 22px}
.card h3{font-size:17px;font-weight:700}
.card time{display:block;font-size:12px;color:var(--date-blue);margin-top:8px}
.card time.red{color:var(--date-red)}
.card p{font-size:12.5px;line-height:20px;margin-top:12px}
.card .btn{width:130px;height:38px;margin-top:18px;font-size:12.5px}

/* stats */
.stats{top:2292px;height:251px;background:var(--grey-bg);display:flex;justify-content:center;gap:80px;padding-top:52px}
.stat{width:160px;text-align:center}
.stat svg{height:74px}
.stat strong{display:block;font-family:'Montserrat',sans-serif;font-size:38px;font-weight:700;color:var(--ink);margin-top:8px}
.stat span{display:block;font-family:'Montserrat',sans-serif;font-size:15px;font-weight:600;color:var(--ink);text-transform:uppercase;margin-top:4px}

/* connect */
.connect{top:2543px;height:270px;background:#fff;text-align:center}
.connect h2{padding-top:44px;font-size:32px}
.social{display:flex;justify-content:center;gap:27px;margin-top:24px}
.social span{width:68px;height:66px;display:flex;align-items:center;justify-content:center;color:#fff;font-family:'Montserrat',sans-serif;font-weight:600;font-size:11px}
.s1{background:#1a4e8a}.s2{background:#2196e6}.s3{background:#0b5a8c}.s4{background:#3ec3d5}.s5{background:#e53935}
.connect .email{margin-top:26px;font-family:'Montserrat',sans-serif;font-size:21px;font-weight:500;color:#555}

/* contact */
.contact{top:2813px;height:409px;background:var(--blue);color:#fff}
.contact h3{position:absolute;color:#fff;font-size:22px;font-weight:700;top:52px}
.form{position:absolute;left:192px;top:110px;width:360px}
.field{border-bottom:1.5px solid #fff;font-size:13px;padding-bottom:4px;color:#fff}
.form .pair{display:flex;gap:30px}
.form .pair .field{flex:1}
.form .field+.field,.form .pair+.field{margin-top:22px}
.form .msg{height:110px}
.form .btn{position:absolute;right:0;top:232px;width:86px;height:38px;font-size:13px}
.addr{position:absolute;left:622px;top:100px;font-size:16px;line-height:24px;display:flex;gap:30px}
.addr div{display:flex;gap:6px}
.map{position:absolute;left:614px;top:197px;width:511px;height:168px;background:linear-gradient(135deg,#e6e9ec,#f3f1ec 60%,#dfe6e0)}

/* footer */
.site-footer{top:3222px;height:142px;background:var(--navy-deep);text-align:center}
.site-footer nav{padding-top:45px;display:flex;justify-content:center;gap:38px}
.site-footer nav a{color:#fff;font-size:17px;text-decoration:none}
.site-footer p{color:#fff;font-size:14px;margin-top:18px}
</style>
</head>
<body>

<header class="hero">
  <div class="hero-photo" role="img" aria-label="Dimmed photo of colleagues working at an office"></div>
  <h1>Welcome To GridWaveform</h1>
  <p>Business 2 Business Solutions</p>
  <div class="slider-dots"><span></span><span></span><span></span><span></span></div>
  <aside class="sidebar">
    <nav class="side-nav">
      <span class="active"><svg width="16" height="16" viewBox="0 0 16 16"><path d="M8 2 1 8h2v6h4v-4h2v4h4V8h2z" fill="#fff"/></svg></span>
      <span><svg width="16" height="16" viewBox="0 0 16 16"><circle cx="8" cy="5" r="3.5" fill="#fff"/><path d="M1 15c0-4 3-6 7-6s7 2 7 6z" fill="#fff"/></svg></span>
      <span><svg width="16" height="16" viewBox="0 0 16 16"><circle cx="8" cy="8" r="5" fill="none" stroke="#fff" stroke-width="3" stroke-dasharray="3 2"/><circle cx="8" cy="8" r="2" fill="#fff"/></svg></span>
      <span><svg width="16" height="16" viewBox="0 0 16 16"><rect x="2" y="4" width="9" height="11" fill="#fff"/><rect x="5" y="1" width="9" height="11" fill="none" stroke="#fff" stroke-width="1.5"/></svg></span>
      <span><svg width="16" height="16" viewBox="0 0 16 16"><rect x="1" y="3" width="14" height="10" fill="#fff"/><path d="M1 3l7 6 7-6" fill="none" stroke="#1b2a44" stroke-width="1.3"/></svg></span>
      <span style="margin-top:10px"><svg width="28" height="20" viewBox="0 0 28 20"><path d="M0 2h28M0 10h28M0 18h28" stroke="#fff" stroke-width="2.5"/></svg></span>
    </nav>
  </aside>
  <div class="brand"><span class="brand-dot"></span><span class="brand-name">GridWaveform</span></div>
</header>

<section class="about">
  <svg class="about-blue" width="1200" height="480" viewBox="0 0 1200 480"><polygon points="0,0 500,0 625,480 0,480" fill="#2196e6"/></svg>
  <div class="about-photo" role="img" aria-label="Photo of a team gathered around a computer monitor">
    <div class="play"><svg width="20" height="22" viewBox="0 0 20 22"><path d="M2 1l17 10L2 21z" fill="#1b2a44"/></svg></div>
  </div>
  <h2>About Us</h2>
  <p>Sed ut perspiciatis unde omnis iste natus error sit volupta­tem accusantium doloremque laudantium, totam rem aperiam, eaque ipsa quae ab illo inventore veritatis et quasi architecto beatae vitae dicta sunt explicabo. Nemo enim ipsam voluptatem quia voluptas sit aspernatur aut odit aut fugit.</p>
  <a class="btn">Read More</a>
</section>

<section class="services">
  <h2 class="sec-title">Managed Services Overview</h2>
  <div class="sec-rule"></div>
  <p class="lead">Sed ut perspiciatis unde omnis iste natus error sit voluptatem accusantium doloremque laudantium, totam rem aperiam, eaque ipsa quae ab illo inventore veritatis et quasi architecto beatae vitae dicta sunt</p>
  <div class="svc-row">
    <div class="svc">
      <svg width="54" height="54" viewBox="0 0 54 54"><g fill="#3a3a3a"><circle cx="27" cy="27" r="17"/><g stroke="#3a3a3a" stroke-width="8"><path d="M27 4v46M4 27h46M11 11l32 32M43 11 11 43"/></g></g><circle cx="27" cy="27" r="7" fill="#f2f2f2"/></svg>
      <h3>Finibus Bonorum</h3>
      <p>Excepteur sint occaecat cupidatat non proident, sunt in culpa</p>
    </div>
    <div class="svc">
      <svg width="54" height="54" viewBox="0 0 54 54"><path d="M27 4a15 15 0 0 0-9 27v7h18v-7A15 15 0 0 0 27 4z" fill="#3a3a3a"/><rect x="19" y="41" width="16" height="4" fill="#3a3a3a"/><rect x="21" y="47" width="12" height="4" rx="2" fill="#3a3a3a"/></svg>
      <h3>Lorem Ipsum passage</h3>
      <p>Excepteur sint occaecat cupidatat non proident, sunt in culpa</p>
    </div>
    <div class="svc">
      <svg width="60" height="54" viewBox="0 0 60 54"><rect x="10" y="8" width="40" height="28" rx="2" fill="none" stroke="#3a3a3a" stroke-width="4"/><path d="M2 42h56l-4 6H6z" fill="#3a3a3a"/></svg>
      <h3>Finibus Bonorum</h3>
      <p>Sed ut perspiciatis unde omnis iste natus error sit voluptatem</p>
    </div>
  </div>
  <a class="btn view">View All Services</a>
  <div class="dots"><span></span><span></span><span></span><span></span></div>
</section>

<section class="partners">
  <svg width="16" height="22" viewBox="0 0 16 22"><path d="M13 2 4 11l9 9" fill="none" stroke="#222" stroke-width="3"/></svg>
  <ul>
    <li>Marlowe Foods</li><li>Steelbrook</li><li>Kinfold Care</li><li>Ostrava Credit</li><li>Platewise</li>
  </ul>
  <svg width="16" height="22" viewBox="0 0 16 22"><path d="m3 2 9 9-9 9" fill="none" stroke="#222" stroke-width="3"/></svg>
</section>

<section class="news">
  <h2 class="sec-title">News And Events</h2>
  <div class="sec-rule"></div>
  <div class="cards">
    <article class="card">
      <div class="card-img" role="img" aria-label="Photo of a businessman in conversation" style="background:linear-gradient(135deg,#8d9aa6,#2c3a4c)"></div>
      <div class="card-body"><h3>Euismod aliquam nulla non</h3><time>APR 27, 2018</time><p>Consequat placerat egestas est quis et tempor ligula vivamus. Officia nullam metus ligula dapibus phasellus amet tincidunt enim varius...</p><a class="btn">Read More</a></div>
    </article>
    <article class="card">
      <div class="card-img" role="img" aria-label="Photo of a support agent wearing a headset" style="background:linear-gradient(135deg,#6b5a4e,#c9b3a0)"></div>
      <div class="card-body"><h3>Euismod aliquam nulla non</h3><time>APR 27, 2018</time><p>Consequat placerat egestas est quis et tempor ligula vivamus. Officia nullam metus ligula dapibus phasellus amet tincidunt enim varius...</p><a class="btn">Read More</a></div>
    </article>
    <article class="card">
      <div class="card-img" role="img" aria-label="Photo of a team meeting around a conference table" style="background:linear-gradient(135deg,#d7d6d2,#8d8474)"></div>
      <div class="card-body"><h3>Euismod aliquam nulla non</h3><time class="red">APR 27, 2018</time><p>Consequat placerat egestas est quis et tempor ligula vivamus. Officia nullam metus ligula dapibus phasellus amet tincidunt enim varius...</p><a class="btn">Read More</a></div>
    </article>
  </div>
</section>

<section class="stats">
  <div class="stat">
    <svg width="74" height="74" viewBox="0 0 74 74" fill="none" stroke="#333" stroke-width="3"><path d="M14 42V34a23 23 0 0 1 46 0v8"/><rect x="8" y="38" width="12" height="20" rx="4"/><rect x="54" y="38" width="12" height="20" rx="4"/><path d="M60 58q0 10-16 10"/></svg>
    <strong>258</strong><span>Consultant</span>
  </div>
  <div class="stat">
    <svg width="80" height="74" viewBox="0 0 80 74" fill="none" stroke="#333" stroke-width="2.5"><circle cx="22" cy="14" r="7"/><circle cx="40" cy="10" r="7"/><circle cx="58" cy="14" r="7"/><path d="M10 38q0-14 12-14t12 14M28 32q0-14 12-14t12 14M46 38q0-14 12-14t12 14"/><path d="M20 50l3 6 6 1-5 4 1 6-5-3-5 3 1-6-5-4 6-1zM40 50l3 6 6 1-5 4 1 6-5-3-5 3 1-6-5-4 6-1zM60 50l3 6 6 1-5 4 1 6-5-3-5 3 1-6-5-4 6-1z"/></svg>
    <strong>124</strong><span>Clients</span>
  </div>
  <div class="stat">
    <svg width="74" height="74" viewBox="0 0 74 74" fill="none" stroke="#333" stroke-width="2.5"><path d="M6 6h62M37 2v4"/><rect x="10" y="6" width="54" height="38"/><path d="M37 44v14M37 58l-10 12M37 58l10 12"/><path d="M37 14l3 7 7 1-5 5 1 7-6-3-6 3 1-7-5-5 7-1z"/></svg>
    <strong>270</strong><span>Projects</span>
  </div>
  <div class="stat">
    <svg width="74" height="74" viewBox="0 0 74 74" fill="none" stroke="#333" stroke-width="2.5"><path d="M10 20 34 8l24 12-24 12zM10 20v28l24 12V32M58 20v16"/><circle cx="54" cy="54" r="12"/><path d="m48 54 4 4 8-8"/></svg>
    <strong>680</strong><span>Donuts Ordered</span>
  </div>
</section>

<section class="connect">
  <h2>Connect with us</h2>
  <div class="social">
    <span class="s1">Friendwall</span>
    <span class="s2">Chirper</span>
    <span class="s3">Worknet</span>
    <span class="s4"><svg width="30" height="22" viewBox="0 0 30 22"><rect x="2" y="2" width="26" height="18" rx="2" fill="none" stroke="#fff" stroke-width="2.5"/><path d="m2 3 13 10L28 3" fill="none" stroke="#fff" stroke-width="2.5"/></svg></span>
    <span class="s5">Streamly</span>
  </div>
  <p class="email">Email : info@verdantledger-hq.net</p>
</section>

<section class="contact">
  <h3 style="left:192px">Contact Us</h3>
  <form class="form">
    <div class="pair"><div class="field">Name *</div><div class="field">Email *</div></div>
    <div class="field">Subject</div>
    <div class="field msg">Message</div>
    <a class="btn">Send</a>
  </form>
  <h3 style="left:622px">Our Address</h3>
  <div class="addr">
    <div><svg width="14" height="18" viewBox="0 0 14 18"><path d="M7 1a6 6 0 0 0-6 6c0 5 6 10 6 10s6-5 6-10a6 6 0 0 0-6-6z" fill="#fff"/><circle cx="7" cy="7" r="2.2" fill="#2196e6"/></svg><span>#123 Lorium ipsum dolor<br>amit, City name</span></div>
    <div style="flex-direction:column;gap:12px">
      <div><svg width="14" height="14" viewBox="0 0 14 14"><path d="M3 1l3 3-2 2q2 3 4 4l2-2 3 3-2 2Q4 12 1 3z" fill="#fff"/></svg><span>Phone : 1-800 555 0142</span></div>
      <div><svg width="14" height="14" viewBox="0 0 14 14"><rect x="3" y="1" width="8" height="4" fill="#fff"/><rect x="1" y="5" width="12" height="8" fill="#fff"/></svg><span>Fax : 1-800 555 0187</span></div>
    </div>
  </div>
  <div class="map" role="img" aria-label="Street map showing the office location"></div>
</section>

<footer class="site-footer">
  <nav><a>Home</a><a>About Us</a><a>Services</a><a>News</a><a>Testimonials</a><a>Contact Us</a></nav>
  <p>© 2018 w.verdantledger.com | Privacy policy</p>
</footer>

</body>
</html>
```